Website for a new t-shirt company called bolddawnapperal.com

We are looking for a talented web designer to create a website that aligns with our brand's message and identity centered around the theme of "Bold Dawn." The website should be modern, clean, and visually appealing while also being user-friendly and easy to navigate.

We will be using the Big Commerce platform for our online store section, so the designer should have experience in designing websites on this platform.

We would like the website to have the following elements:

A color scheme that aligns with the brand's identity and message
A homepage that showcases our products and message, with clear calls-to-action for visitors to explore further
A blog section that highlights our brand's philosophy and offers advice and tips for people looking to make positive changes in their lives
An "About Us" section that introduces our brand and team and offers insight into our mission and values
A contact form that allows visitors to easily get in touch with us for inquiries or support
We are open to creative suggestions and ideas from the designer, but we would like the website to have a modern and minimalist aesthetic that resonates with our target audience of 20 to 40-year-olds.

```html
<!DOCTYPE html>
<html lang="en">
<head>
<meta charset="utf-8">
<title>Bold Dawn — Apparel</title>
<link href="https://fonts.googleapis.com/css2?family=Niconne&family=Inter:wght@400;500;600&display=swap" rel="stylesheet">
<style>
:root{
  --ink:#111111;
  --text:#2b2b2b;
  --muted:#555555;
  --paper:#ffffff;
  --soft:#f2f2f2;
  --foot:#ebebeb;
  --star:#f4b400;
  --line:#d8d8d8;
}
*{box-sizing:border-box;margin:0;padding:0}
html,body{width:1200px;height:5231px;overflow:hidden;background:var(--paper)}
body{position:relative;font-family:'Inter',sans-serif;color:var(--text)}
.abs{position:absolute}
.script{font-family:'Niconne',cursive;color:var(--ink);font-weight:400;white-space:nowrap}
.center{left:0;width:1200px;text-align:center}
.sec-title{font-size:38px}
.sec-sub{font-size:14px;color:var(--ink)}
.sec-rule{width:110px;height:1px;background:var(--ink);left:545px}
.arrow{width:48px;height:48px;border-radius:50%;background:var(--paper);display:flex;align-items:center;justify-content:center;box-shadow:0 2px 6px rgba(0,0,0,.12)}
.arrow.dark{background:var(--ink)}
.photo{border-radius:4px}
.social{display:flex;gap:18px}
.dot{width:11px;height:11px;border-radius:50%;background:var(--ink);display:inline-block}
.nav{display:flex;gap:38px;font-size:14px;font-weight:500;color:var(--ink);top:97px;left:326px}
.promo{top:146px;left:0;width:1200px;height:51px;background:var(--ink);color:#fff;font-size:13px;font-weight:600;display:flex;align-items:center;justify-content:center}
.col-label{font-size:28px}
.count{font-size:15px;color:var(--ink)}
.p-name{font-size:27px}
.p-price{font-size:19px;color:var(--ink)}
.p-meta{font-size:14px;color:var(--ink);display:flex;align-items:center;gap:4px}
.swatch{width:12px;height:12px;border-radius:50%;display:inline-block}
.tool{width:42px;height:42px;background:#fff;border-radius:6px;display:flex;align-items:center;justify-content:center}
.val-title{font-size:29px}
.val-sub{font-size:14px;color:var(--ink)}
.quote{font-size:15px;line-height:38px;color:var(--text)}
.avatar{width:72px;height:72px;border-radius:50%}
.t-name{font-size:29px}
.t-role{font-size:15px}
.b-date{font-size:21px;background:#fff;padding:0 8px;border-radius:0 0 4px 0}
.b-title{font-size:28px}
.b-text{font-size:15px;line-height:38px}
.b-more{font-size:21px}
.contact{top:4210px;left:0;width:1200px;height:555px;background:var(--ink)}
.field{border:1.5px solid #fff;border-radius:4px;color:#fff;font-size:14px;padding:0 24px;display:flex;align-items:center;height:63px}
.btn-light{background:#fff;border-radius:5px;display:flex;align-items:center;justify-content:center;font-size:32px}
.footer{top:4765px;left:0;width:1200px;height:466px;background:var(--foot)}
.f-title{font-size:29px}
.f-text{font-size:15px;line-height:38px;color:var(--text)}
.f-link{font-size:15px;color:var(--text)}
.pay{font-size:11px;font-weight:600;color:var(--ink)}
</style>
</head>
<body>

<header>
  <div class="abs social" style="top:40px;left:110px"><span class="dot"></span><span class="dot"></span><span class="dot"></span><span class="dot"></span></div>
  <div class="abs script center" style="top:10px;font-size:50px">Bold Dawn</div>
  <div class="abs" style="top:36px;left:990px;display:flex;gap:22px">
    <svg width="18" height="18" viewBox="0 0 20 20" fill="none" stroke="#111" stroke-width="2"><circle cx="8" cy="8" r="6"/><path d="M13 13l5 5"/></svg>
    <svg width="18" height="18" viewBox="0 0 20 20" fill="none" stroke="#111" stroke-width="2"><circle cx="10" cy="6" r="4"/><path d="M2 19c1-5 15-5 16 0"/></svg>
    <svg width="18" height="18" viewBox="0 0 20 20" fill="none" stroke="#111" stroke-width="2"><rect x="3" y="6" width="14" height="13" rx="1"/><path d="M7 8V4a3 3 0 016 0v4"/></svg>
  </div>
  <nav class="abs nav"><span>HOME</span><span>ABOUT US</span><span>PRODUCTS</span><span>OUR TEAM</span><span>CONTACT US</span></nav>
  <div class="abs promo">50% OFF WITH THE CODE WELCOME!!</div>
</header>

<section>
  <div class="abs" role="img" aria-label="Couple wearing white branded t-shirts and jeans on a light blue background" style="top:197px;left:0;width:1200px;height:568px;background:linear-gradient(90deg,#d3e0ea 0%,#c9dae7 45%,#b9cfe0 65%,#cfdde9 100%)"></div>
  <div class="abs script" style="top:306px;left:154px;font-size:46px;line-height:62px">Discount Flat 10% Off<br>On Latest Clothes</div>
  <div class="abs" style="top:455px;left:154px;font-size:15px;line-height:39px;color:var(--ink)">Sed ut perspiciatis unde omnis iste natus error<br>sit voluptatem accusantium doloremque.</div>
  <div class="abs script" style="top:556px;left:154px;width:222px;height:64px;background:var(--ink);color:#fff;border-radius:6px;display:flex;align-items:center;justify-content:center;font-size:34px">Get Started</div>
  <div class="abs arrow" style="top:457px;left:29px"><svg width="14" height="14" viewBox="0 0 14 14" fill="none" stroke="#111" stroke-width="2"><path d="M9 2L4 7l5 5"/></svg></div>
  <div class="abs arrow" style="top:457px;left:1113px"><svg width="14" height="14" viewBox="0 0 14 14" fill="none" stroke="#111" stroke-width="2"><path d="M5 2l5 5-5 5"/></svg></div>
</section>

<section>
  <div class="abs script center sec-title" style="top:850px">Shop By Collections</div>
  <div class="abs center sec-sub" style="top:913px">An Exceptionally Experience</div>
  <div class="abs sec-rule" style="top:940px"></div>
  <div class="abs photo" role="img" aria-label="Smiling man in white t-shirt on yellow background" style="top:985px;left:124px;width:304px;height:412px;background:linear-gradient(160deg,#f2cb24,#e4b50f)"></div>
  <div class="abs photo" role="img" aria-label="Smiling woman in white sweatshirt on pink background" style="top:985px;left:449px;width:304px;height:412px;background:linear-gradient(160deg,#d9b3b8,#c99fa5)"></div>
  <div class="abs photo" role="img" aria-label="Couple in white t-shirts on light grey background" style="top:985px;left:773px;width:304px;height:412px;background:linear-gradient(160deg,#eeeeee,#dcdcdc)"></div>
  <div class="abs script col-label" style="top:1414px;left:124px">Men's</div><div class="abs count" style="top:1422px;left:348px">20 Items</div>
  <div class="abs script col-label" style="top:1414px;left:449px">Women's</div><div class="abs count" style="top:1422px;left:673px">30 Items</div>
  <div class="abs script col-label" style="top:1414px;left:785px">Shop All</div><div class="abs count" style="top:1422px;left:998px">60 Items</div>
</section>

<section>
  <div class="abs script center sec-title" style="top:1526px">Our Products</div>
  <div class="abs center sec-sub" style="top:1589px">An Exceptionally Experience</div>
  <div class="abs sec-rule" style="top:1616px"></div>
  <div class="abs photo" role="img" aria-label="Cheerful woman in pink t-shirt on pink background" style="top:1665px;left:10px;width:286px;height:422px;background:linear-gradient(160deg,#e6a9bd,#d894aa)"></div>
  <div class="abs photo" role="img" aria-label="Man in checked shirt and jeans on white background" style="top:1665px;left:309px;width:286px;height:422px;background:linear-gradient(160deg,#f1f1f1,#dedede)"></div>
  <div class="abs photo" role="img" aria-label="Man in white shirt on warm beige background" style="top:1665px;left:605px;width:286px;height:422px;background:linear-gradient(160deg,#c3b0a2,#ad988a)"></div>
  <div class="abs photo" role="img" aria-label="Surprised woman in black sweater holding a phone on pink background" style="top:1665px;left:903px;width:287px;height:422px;background:linear-gradient(160deg,#e8a8bd,#d691a8)"></div>
  <div class="abs tool" style="top:1928px;left:696px"><svg width="16" height="16" viewBox="0 0 20 20" fill="none" stroke="#111" stroke-width="2"><circle cx="8" cy="8" r="6"/><path d="M13 13l5 5"/></svg></div>
  <div class="abs tool" style="top:1928px;left:757px"><svg width="16" height="16" viewBox="0 0 20 20" fill="none" stroke="#111" stroke-width="2"><rect x="3" y="6" width="14" height="13" rx="1"/><path d="M7 8V4a3 3 0 016 0v4"/></svg></div>
  <div class="abs arrow" style="top:1852px;left:29px"><svg width="14" height="14" viewBox="0 0 14 14" fill="none" stroke="#111" stroke-width="2"><path d="M9 2L4 7l5 5"/></svg></div>
  <div class="abs arrow" style="top:1852px;left:1113px"><svg width="14" height="14" viewBox="0 0 14 14" fill="none" stroke="#111" stroke-width="2"><path d="M5 2l5 5-5 5"/></svg></div>

  <div class="abs script p-name" style="top:2108px;left:10px">Sed ut perspiciatis</div>
  <div class="abs p-meta" style="top:2120px;left:252px">0 <span style="color:var(--star)">★</span></div>
  <div class="abs p-price" style="top:2156px;left:10px">$56.9</div>
  <div class="abs p-meta" style="top:2153px;left:232px"><span class="swatch" style="background:#1c3b5a"></span><span class="swatch" style="background:#d8232a"></span>+1</div>

  <div class="abs script p-name" style="top:2108px;left:317px">Sed ut perspiciatis</div>
  <div class="abs p-meta" style="top:2120px;left:554px">0 <span style="color:var(--star)">★</span></div>
  <div class="abs p-price" style="top:2156px;left:317px">$125.0</div>
  <div class="abs p-meta" style="top:2153px;left:534px"><span class="swatch" style="background:#6b1f2a"></span><span class="swatch" style="background:#c0582a"></span>+1</div>

  <div class="abs script p-name" style="top:2108px;left:611px">Sed ut perspiciatis</div>
  <div class="abs p-meta" style="top:2120px;left:849px">0 <span style="color:var(--star)">★</span></div>
  <div class="abs p-price" style="top:2156px;left:611px">$125.0</div>
  <div class="abs p-meta" style="top:2153px;left:829px"><span class="swatch" style="background:#111"></span><span class="swatch" style="background:#7f8c1e"></span>+1</div>

  <div class="abs script p-name" style="top:2108px;left:916px">Sed ut perspiciatis</div>
  <div class="abs p-meta" style="top:2120px;left:1147px">0 <span style="color:var(--star)">★</span></div>
  <div class="abs p-price" style="top:2156px;left:916px">$172.2</div>
  <div class="abs p-meta" style="top:2153px;left:1127px"><span class="swatch" style="background:#5bdca0"></span><span class="swatch" style="background:#38c9e0"></span>+1</div>
</section>

<section>
  <div class="abs" role="img" aria-label="Row of colourful t-shirts hanging on a rail, yellow in front" style="top:2262px;left:0;width:1200px;height:457px;background:linear-gradient(100deg,#c99a1c 0%,#a9862e 35%,#7a6a60 55%,#5b6d8a 70%,#8a6a8e 85%,#b98f80 100%)"></div>
  <div class="abs script center" style="top:2342px;font-size:36px;color:#fff">Nemo enim ipsam voluptatem quia voluptas sit</div>
  <div class="abs center" style="top:2415px;font-size:15px;color:#fff">Lorem ipsum dolor sit amet, consectetur adipiscing</div>
  <div class="abs" style="top:2465px;left:572px;width:56px;height:56px;border-radius:50%;background:#fff;display:flex;align-items:center;justify-content:center"><svg width="20" height="22" viewBox="0 0 20 22"><path d="M4 2l14 9-14 9z" fill="#111"/></svg></div>
</section>

<section>
  <svg class="abs" style="top:2808px;left:143px" width="60" height="60" viewBox="0 0 60 60" fill="none" stroke="#111" stroke-width="2"><circle cx="28" cy="32" r="24"/><circle cx="28" cy="32" r="15"/><circle cx="28" cy="32" r="6"/><path d="M28 32L52 8M44 8h8v8"/></svg>
  <div class="abs script val-title" style="top:2806px;left:225px">Our Mission</div>
  <div class="abs val-sub" style="top:2858px;left:225px">Nemo enim ipsam</div>
  <svg class="abs" style="top:2808px;left:500px" width="60" height="60" viewBox="0 0 60 60" fill="none" stroke="#111" stroke-width="2"><circle cx="18" cy="22" r="6"/><circle cx="42" cy="22" r="6"/><path d="M6 56V38c0-6 24-6 24 0v18M30 56V38c0-6 24-6 24 0v18"/><path d="M30 4l2 4 4 1-3 3 1 4-4-2-4 2 1-4-3-3 4-1z"/></svg>
  <div class="abs script val-title" style="top:2806px;left:579px">Our Values</div>
  <div class="abs val-sub" style="top:2858px;left:579px">Nemo enim ipsam</div>
  <svg class="abs" style="top:2808px;left:836px" width="66" height="60" viewBox="0 0 66 60" fill="none" stroke="#111" stroke-width="2"><path d="M4 30c14-20 44-20 58 0-14 20-44 20-58 0z"/><circle cx="33" cy="30" r="10"/><circle cx="33" cy="30" r="3"/><path d="M2 14V4h10M54 4h10v10M64 46v10H54M12 56H2V46"/></svg>
  <div class="abs script val-title" style="top:2806px;left:924px">Our Vision</div>
  <div class="abs val-sub" style="top:2858px;left:924px">Nemo enim ipsam</div>
</section>

<section>
  <div class="abs" style="top:2974px;left:0;width:1200px;height:471px;background:var(--soft)"></div>
  <div class="abs script center sec-title" style="top:3014px">Our Team</div>
  <div class="abs center sec-sub" style="top:3077px">An Exceptionally Experience</div>
  <div class="abs sec-rule" style="top:3104px"></div>

  <div class="abs script" style="top:3158px;left:108px;font-size:40px">“</div>
  <div class="abs quote" style="top:3201px;left:110px">Neque porro quisquam est, qui<br>dolorem ipsum quia dolor sit amet,</div>
  <div class="abs avatar" role="img" aria-label="Portrait of team member" style="top:3297px;left:110px;background:linear-gradient(160deg,#9aa6b4,#5d6774)"></div>
  <div class="abs script t-name" style="top:3296px;left:203px">Lorem ipsum</div>
  <div class="abs t-role" style="top:3344px;left:201px">General Manager</div>

  <div class="abs script" style="top:3158px;left:449px;font-size:40px">“</div>
  <div class="abs quote" style="top:3201px;left:451px">Neque porro quisquam est, qui<br>dolorem ipsum quia dolor sit amet,</div>
  <div class="abs avatar" role="img" aria-label="Portrait of team member" style="top:3297px;left:451px;background:linear-gradient(160deg,#e0e0e0,#7a7a7a)"></div>
  <div class="abs script t-name" style="top:3296px;left:548px">Lorem ipsum</div>
  <div class="abs t-role" style="top:3344px;left:547px">General Manager</div>

  <div class="abs script" style="top:3158px;left:802px;font-size:40px">“</div>
  <div class="abs quote" style="top:3201px;left:804px">Neque porro quisquam est, qui<br>dolorem ipsum quia dolor sit amet,</div>
  <div class="abs avatar" role="img" aria-label="Portrait of team member" style="top:3297px;left:804px;background:linear-gradient(160deg,#c8c8c8,#555)"></div>
  <div class="abs script t-name" style="top:3296px;left:901px">Lorem ipsum</div>
  <div class="abs t-role" style="top:3344px;left:900px">General Manager</div>
</section>

<section>
  <div class="abs script center sec-title" style="top:3528px">Recent Blogs</div>
  <div class="abs center sec-sub" style="top:3591px">An Exceptionally Experience</div>
  <div class="abs sec-rule" style="top:3618px"></div>

  <div class="abs photo" role="img" aria-label="White t-shirt laid on green leaves" style="top:3695px;left:112px;width:314px;height:245px;background:linear-gradient(150deg,#4f7a3a,#2f5a28)"></div>
  <div class="abs script b-date" style="top:3695px;left:112px">28th May</div>
  <div class="abs photo" role="img" aria-label="Man in dark t-shirt in a warmly lit café" style="top:3695px;left:443px;width:314px;height:245px;background:linear-gradient(150deg,#6e6258,#2f2a26)"></div>
  <div class="abs script b-date" style="top:3695px;left:443px">20th Feb</div>
  <div class="abs" style="top:3795px;left:576px;width:46px;height:46px;border-radius:8px;background:#111;display:flex;align-items:center;justify-content:center"><svg width="20" height="20" viewBox="0 0 20 20" fill="none" stroke="#fff" stroke-width="2"><path d="M8 12l4-4M7 9l-2 2a3 3 0 004 4l2-2M13 11l2-2a3 3 0 00-4-4L9 7"/></svg></div>
  <div class="abs photo" role="img" aria-label="White t-shirt on a hanger against dark wood" style="top:3695px;left:773px;width:315px;height:245px;background:linear-gradient(150deg,#4a3a30,#221a15)"></div>
  <div class="abs script b-date" style="top:3695px;left:773px">12th Sep</div>

  <div class="abs arrow dark" style="top:3851px;left:33px"><svg width="14" height="14" viewBox="0 0 14 14" fill="none" stroke="#fff" stroke-width="2"><path d="M9 2L4 7l5 5"/></svg></div>
  <div class="abs arrow dark" style="top:3851px;left:1119px"><svg width="14" height="14" viewBox="0 0 14 14" fill="none" stroke="#fff" stroke-width="2"><path d="M5 2l5 5-5 5"/></svg></div>

  <div class="abs script b-title" style="top:3970px;left:112px">At vero eos et accusamus</div>
  <div class="abs b-text" style="top:4015px;left:112px">Neque porro quisquam est, qui<br>dolorem ipsum quia dolor sit amet,</div>
  <div class="abs script b-more" style="top:4096px;left:112px">Read More</div>

  <div class="abs script b-title" style="top:3970px;left:443px">At vero eos et accusamus</div>
  <div class="abs b-text" style="top:4015px;left:443px">Neque porro quisquam est, qui<br>dolorem ipsum quia dolor sit amet,</div>
  <div class="abs script b-more" style="top:4096px;left:443px">Read More</div>

  <div class="abs script b-title" style="top:3970px;left:773px">At vero eos et accusamus</div>
  <div class="abs b-text" style="top:4015px;left:773px">Neque porro quisquam est, qui<br>dolorem ipsum quia dolor sit amet,</div>
  <div class="abs script b-more" style="top:4096px;left:773px">Read More</div>
</section>

<section>
  <div class="abs contact"></div>
  <div class="abs script center sec-title" style="top:4255px;color:#fff">Get In Touch</div>
  <div class="abs field" style="top:4349px;left:205px;width:374px">Last Name</div>
  <div class="abs field" style="top:4349px;left:623px;width:376px">First Name</div>
  <div class="abs field" style="top:4444px;left:205px;width:374px">Email Address</div>
  <div class="abs field" style="top:4444px;left:623px;width:376px">Phone Number</div>
  <div class="abs field" style="top:4541px;left:205px;width:794px">Message...</div>
  <div class="abs script btn-light" style="top:4649px;left:505px;width:189px;height:65px">Contact Us</div>
</section>

<footer>
  <div class="abs footer"></div>
  <div class="abs script f-title" style="top:4840px;left:110px">About Us</div>
  <div class="abs f-text" style="top:4894px;left:110px">Nemo enim ipsam voluptatem quia voluptas<br>sit aspernatur aut odit aut fugit, sed quia<br>consequuntur magni dolores eos qui ratione<br>voluptatem sequi nesciunt. Neque porro<br>quisquam est, qui dolorem ipsum quia dolor</div>
  <div class="abs social" style="top:5109px;left:110px"><span class="dot"></span><span class="dot"></span><span class="dot"></span><span class="dot"></span></div>

  <div class="abs script f-title" style="top:4840px;left:564px">Quick Links</div>
  <div class="abs f-link" style="top:4913px;left:564px">Home</div>
  <div class="abs f-link" style="top:4958px;left:564px">About Us</div>
  <div class="abs f-link" style="top:5002px;left:564px">Products</div>
  <div class="abs f-link" style="top:5047px;left:564px">Our Team</div>
  <div class="abs f-link" style="top:5091px;left:564px">Contact Us</div>

  <div class="abs script f-title" style="top:4840px;left:804px">Contact Us</div>
  <svg class="abs" style="top:4911px;left:806px" width="16" height="20" viewBox="0 0 16 20"><path d="M8 0a7 7 0 00-7 7c0 5 7 13 7 13s7-8 7-13a7 7 0 00-7-7z" fill="#111"/><circle cx="8" cy="7" r="2.5" fill="#ebebeb"/></svg>
  <div class="abs f-link" style="top:4913px;left:834px">14 Kestrel Row, Dunmore,</div>
  <svg class="abs" style="top:4965px;left:806px" width="16" height="16" viewBox="0 0 16 16"><path d="M3 1l3 3-2 2c1 2 3 4 5 5l2-2 3 3-2 3C7 15 1 9 0 4z" fill="#111"/></svg>
  <div class="abs f-link" style="top:4963px;left:834px">+1 555 014 2277</div>

  <div class="abs" style="top:5161px;left:0;width:1200px;height:1px;background:var(--line)"></div>
  <div class="abs" style="top:5189px;left:110px;font-size:14px;color:var(--ink)">©2023 COPYRIGHTS. BOLD DAWN. ALL RIGHTS RESERVED.</div>
  <div class="abs" style="top:5190px;left:846px;display:flex;gap:18px">
    <span class="pay">Quenda</span><span class="pay">Harlo</span><span class="pay">Tovimark</span><span class="pay">Pinewell</span><span class="pay">Orvel</span>
  </div>
</footer>

</body>
</html>
```